Business Card for Air Cargo Brokerage

Hi Craftquorum -

Please see the images attached. I need a business card with a similar image and format but modernized. Business card should be portrait and have room for a QR code.

Thanks

```html
<!DOCTYPE html>
<html lang="en">
<head>
<meta charset="UTF-8">
<title>Skyward Freight – Business Card</title>
<link href="https://fonts.googleapis.com/css2?family=Open+Sans:wght@400;600;700;800&display=swap" rel="stylesheet">
<style>
  :root {
    --canvas: #1a1a1a;
    --card: #262626;
    --card-edge: #303030;
    --ink-bright: #f2f2f2;
    --ink-soft: #d6d6d6;
    --ink-muted: #9a9a9a;
    --rule: #6a6a6a;
  }
  * { margin: 0; padding: 0; box-sizing: border-box; }
  html, body {
    width: 1200px; height: 939px; overflow: hidden;
    background: var(--canvas);
    font-family: "Open Sans", Arial, sans-serif;
  }
  .canvas { position: relative; width: 1200px; height: 939px; }
  .card {
    position: absolute;
    width: 320px; height: 560px;
    border-radius: 24px;
    background: var(--card);
    border: 1px solid var(--card-edge);
  }
  .card--front { left: 250px; top: 190px; }
  .card--back { left: 630px; top: 190px; }

  /* Front */
  .brand {
    position: absolute; left: 0; right: 0; top: 200px;
    display: flex; flex-direction: column; align-items: center;
    text-align: center;
  }
  .brand__mark {
    width: 58px; height: 58px; border-radius: 50%;
    background: var(--ink-muted); margin-bottom: 24px;
  }
  .brand__name {
    font-weight: 800; font-size: 30px; letter-spacing: -0.5px;
    color: var(--ink-bright); line-height: 1;
  }
  .brand__tagline {
    margin-top: 12px; font-size: 12px; letter-spacing: 1px;
    color: var(--ink-soft); text-transform: uppercase;
  }

  /* Back */
  .corner-mark {
    position: absolute; right: 36px; top: 36px;
    width: 34px; height: 34px; border-radius: 50%;
    background: var(--ink-muted);
  }
  .person { position: absolute; left: 40px; top: 150px; }
  .person__name {
    font-weight: 700; font-size: 25px; letter-spacing: 1px;
    color: var(--ink-muted); line-height: 1.1;
  }
  .person__role { font-size: 15px; color: var(--ink-soft); margin-top: 4px; }
  .divider {
    position: absolute; left: 40px; top: 232px;
    width: 48px; height: 1px; background: var(--rule);
  }
  .contact { position: absolute; left: 40px; top: 250px; list-style: none; }
  .contact__item {
    display: flex; align-items: center; gap: 10px;
    font-size: 15px; color: var(--ink-soft); line-height: 28px;
  }
  .contact__icon { width: 12px; height: 12px; fill: var(--ink-muted); flex: none; }
  .qr-space {
    position: absolute; left: 40px; top: 396px;
    width: 120px; height: 120px;
    border: 1px solid var(--rule); border-radius: 6px;
  }
</style>
</head>
<body>
<div class="canvas">
  <section class="card card--front">
    <div class="brand">
      <span class="brand__mark"></span>
      <span class="brand__name">Skyward Freight</span>
      <span class="brand__tagline">Solutions for global air commerce</span>
    </div>
  </section>

  <section class="card card--back">
    <span class="corner-mark"></span>
    <div class="person">
      <div class="person__name">DANIEL REYES</div>
      <div class="person__role">Founder &amp; CEO</div>
    </div>
    <span class="divider"></span>
    <ul class="contact">
      <li class="contact__item">
        <svg class="contact__icon" viewBox="0 0 24 24"><path d="M6.6 10.8a15.1 15.1 0 0 0 6.6 6.6l2.2-2.2a1 1 0 0 1 1-.25 11.4 11.4 0 0 0 3.6.57 1 1 0 0 1 1 1V20a1 1 0 0 1-1 1A17 17 0 0 1 3 4a1 1 0 0 1 1-1h3.5a1 1 0 0 1 1 1c0 1.25.2 2.45.57 3.6a1 1 0 0 1-.25 1z"/></svg>
        (555) 204-3318
      </li>
      <li class="contact__item">
        <svg class="contact__icon" viewBox="0 0 24 24"><path d="M2 5h20v14H2z"/><path d="M2 6l10 7 10-7v-1H2z" fill="#262626"/></svg>
        info@skywardfreight.com
      </li>
      <li class="contact__item">
        <svg class="contact__icon" viewBox="0 0 24 24"><circle cx="12" cy="12" r="10"/><path d="M12 2v20M2 12h20" stroke="#262626" stroke-width="1.6"/></svg>
        skywardfreight.com
      </li>
    </ul>
    <div class="qr-space" aria-label="Reserved space for QR code"></div>
  </section>
</div>
</body>
</html>
```